A clean crisp business card for a Landscape Construction company. Designed to be easy to read contact/ info and also be appealing/interesting, unlike a traditional business card.

Industry/Entity Type

Landscape Construction

Contact Information for Business Card

Company name : Brambleford Landscape Construction, phone number: (877) 62Vista, website:Bramblefordyards.example, Email, sales@bramblefordyards.example

Requirements
Nice to have
• Luxurious finishes/ details…. Icons or emblems next to contact info
Should not have
• Clipart or general pictures

```html
<!DOCTYPE html>
<html lang="en">
<head>
<meta charset="utf-8">
<title>Brambleford Landscape Construction – Business Card</title>
<link rel="stylesheet" href="https://fonts.googleapis.com/css2?family=Cinzel:wght@400;600&family=Arimo:wght@400&display=swap">
<style>
  :root {
    --backdrop: #d9d6d2;
    --card-black: #0e0e0e;
    --card-white: #ffffff;
    --brand-blue: #2a6fc9;
    --brand-green: #8cc63f;
    --ink-light: #f2f2f2;
  }
  * { margin: 0; padding: 0; box-sizing: border-box; }
  html, body { width: 1200px; height: 716px; overflow: hidden; }
  body {
    background: var(--backdrop);
    position: relative;
    font-family: "Arimo", Arial, sans-serif;
  }
  .card {
    position: absolute;
    top: 208px;
    width: 540px;
    height: 300px;
    box-shadow: 0 10px 28px rgba(0,0,0,.25);
    overflow: hidden;
  }
  .card--front { left: 30px; background: var(--card-black); }
  .card--back { left: 630px; background: var(--card-white); }

  .brand {
    position: absolute;
    font-family: "Cinzel", Georgia, serif;
    font-weight: 600;
    color: var(--brand-blue);
    text-align: center;
    line-height: 1.15;
    display: flex;
    align-items: center;
    gap: 10px;
  }
  .brand__dot {
    width: 14px; height: 14px; border-radius: 50%;
    background: var(--brand-green);
    flex: none;
  }
  .card--front .brand {
    left: 0; right: 0; top: 110px;
    justify-content: center;
    font-size: 30px;
  }
  .card--front .brand small { display: block; font-size: 13px; letter-spacing: 3px; }

  .back-shape { position: absolute; inset: 0; }

  .card--back .brand {
    right: 26px; top: 100px;
    font-size: 24px;
  }
  .card--back .brand small { display: block; font-size: 11px; letter-spacing: 2.5px; }

  .person {
    position: absolute;
    left: 26px; top: 150px;
    font-family: "Cinzel", Georgia, serif;
  }
  .person__name { color: var(--brand-blue); font-size: 19px; letter-spacing: 1px; }
  .person__role { color: var(--brand-green); font-size: 13px; letter-spacing: 1px; margin-top: 2px; }

  .contact {
    position: absolute;
    left: 26px; top: 210px;
    list-style: none;
    color: var(--ink-light);
    font-size: 12px;
  }
  .contact li { display: flex; align-items: center; gap: 7px; margin-bottom: 5px; }
  .contact svg { width: 11px; height: 11px; flex: none; }
</style>
</head>
<body>

  <section class="card card--front" aria-label="Card front">
    <div class="brand">
      <span class="brand__dot"></span>
      <span>Brambleford<small>Landscape Construction</small></span>
    </div>
  </section>

  <section class="card card--back" aria-label="Card back">
    <svg class="back-shape" viewBox="0 0 540 300" preserveAspectRatio="none" aria-hidden="true">
      <path d="M0 40 C120 60 200 110 260 200 C300 262 380 292 540 292 L540 300 L0 300 Z" fill="var(--card-black)"/>
      <path d="M0 40 C120 60 200 110 260 200 C300 262 380 292 540 292" fill="none" stroke="var(--card-white)" stroke-width="14"/>
      <path d="M0 32 C120 52 200 102 260 192 C300 254 380 282 540 282" fill="none" stroke="var(--brand-blue)" stroke-width="7"/>
      <path d="M270 205 C320 262 400 282 540 272" fill="none" stroke="var(--brand-green)" stroke-width="9"/>
    </svg>

    <div class="brand">
      <span class="brand__dot"></span>
      <span>Brambleford<small>Landscape Construction</small></span>
    </div>

    <div class="person">
      <p class="person__name">Daniel Avery</p>
      <p class="person__role">Director</p>
    </div>

    <ul class="contact">
      <li>
        <svg viewBox="0 0 12 12"><path d="M3 1 L5 3.5 L4 5 C4.6 6.4 5.6 7.4 7 8 L8.5 7 L11 9 L10 11 C5 11 1 7 1 2 Z" fill="var(--brand-green)"/></svg>
        (877) 62Vista
      </li>
      <li>
        <svg viewBox="0 0 12 12"><rect x="1" y="2.5" width="10" height="7" fill="none" stroke="var(--brand-green)" stroke-width="1.2"/><path d="M1 2.5 L6 6.5 L11 2.5" fill="none" stroke="var(--brand-green)" stroke-width="1.2"/></svg>
        sales@bramblefordyards.example
      </li>
      <li>
        <svg viewBox="0 0 12 12"><circle cx="6" cy="6" r="5" fill="none" stroke="var(--brand-green)" stroke-width="1.2"/><path d="M1 6 H11 M6 1 C3.5 4 3.5 8 6 11 M6 1 C8.5 4 8.5 8 6 11" fill="none" stroke="var(--brand-green)" stroke-width="1"/></svg>
        www.bramblefordyards.example
      </li>
    </ul>
  </section>

</body>
</html>
```